Lo Mara Menu Design Project

This project is pretty straight forward. You will be given 3 files which include the following:
1. Our proposed menu
2. Our Company logo
3. A sample menu on what we are looking for design wise

Your job is to create a visually pleasing menu that is simple, clean and fresh. Please refer to our home website for additional information. (www.lomara-eats.com) Must be in eps or equivalent format.

Target Market(s)

20s to 40s

Industry/Entity Type

It Company

Requirements
Must have
• Company log
Must be in EPS format

```html
<!DOCTYPE html>
<html lang="en">
<head>
<meta charset="UTF-8">
<title>Lo Mara Menu – Salads &amp; Chicken</title>
<link rel="stylesheet" href="https://fonts.googleapis.com/css2?family=Josefin+Sans:ital,wght@0,400;0,600;0,700;1,300;1,400&display=swap">
<style>
  :root {
    --bg: #000000;
    --ink: #ffffff;
    --red: #c8102e;
    --rule: #b3121f;
    --motif: #5c0b10;
  }
  * { margin: 0; padding: 0; box-sizing: border-box; }
  html, body { width: 1200px; height: 1000px; overflow: hidden; background: var(--bg); }
  .menu {
    position: relative;
    width: 1200px;
    height: 1000px;
    background: var(--bg);
    color: var(--ink);
    font-family: "Josefin Sans", "Century Gothic", sans-serif;
    overflow: hidden;
  }
  .motif { position: absolute; left: 0; top: 0; width: 1200px; height: 1000px; }
  .section-title {
    position: absolute;
    left: 0; width: 1200px;
    text-align: center;
    color: var(--red);
    font-size: 23px;
    font-weight: 400;
    letter-spacing: 0.5px;
  }
  .section-note {
    position: absolute;
    text-align: center;
    font-style: italic;
    font-weight: 300;
    font-size: 19px;
    line-height: 25px;
  }
  .salad {
    position: absolute;
    top: 106px;
    width: 370px;
    text-align: center;
  }
  .salad-name { font-size: 19px; font-weight: 600; line-height: 25px; }
  .salad-name .price { margin-left: 12px; }
  .desc {
    font-style: italic;
    font-weight: 300;
    font-size: 18.5px;
    line-height: 25px;
  }
  .rule-h { position: absolute; left: 48px; top: 253px; width: 1102px; height: 3px; background: var(--rule); }
  .rule-v { position: absolute; left: 600px; top: 312px; width: 3px; height: 670px; background: var(--rule); }
  .column { position: absolute; }
  .column--left { left: 46px; top: 433px; width: 508px; }
  .column--right { left: 658px; top: 313px; width: 494px; }
  .item-head {
    display: flex;
    justify-content: space-between;
    font-size: 19px;
    font-weight: 600;
    line-height: 25px;
  }
  .item .desc { padding-left: 37px; }
  .item .desc--flush { padding-left: 0; }
  .brand {
    position: absolute;
    top: 934px;
    display: flex;
    align-items: center;
    gap: 6px;
    color: var(--red);
    font-size: 17px;
    font-weight: 700;
  }
  .brand-mark { width: 12px; height: 12px; background: var(--red); }
</style>
</head>
<body>
<main class="menu">
  <svg class="motif" viewBox="0 0 1200 1000" role="img" aria-label="Large faint dark red decorative cloud-swirl motif behind the menu">
    <defs>
      <radialGradient id="motifGlow" cx="0.5" cy="0.5" r="0.5">
        <stop offset="0" stop-color="#5c0b10" stop-opacity="0.95"/>
        <stop offset="0.7" stop-color="#4a080c" stop-opacity="0.7"/>
        <stop offset="1" stop-color="#000000" stop-opacity="0"/>
      </radialGradient>
    </defs>
    <ellipse cx="610" cy="520" rx="520" ry="360" fill="url(#motifGlow)"/>
  </svg>

  <h2 class="section-title" style="top:30px;">SALADS</h2>
  <p class="section-note" style="left:0; width:1200px; top:58px;">Can replace Chicken with Tofu for $1.50</p>

  <article class="salad" style="left:37px;">
    <h3 class="salad-name">Chinese Chicken Salad<span class="price">10.50</span></h3>
    <p class="desc">Shredded lettuce, chicken breast, carrots, toasted almonds, browncrunchies, and white crunchies with tart red ginger dressing</p>
  </article>
  <article class="salad" style="left:413px;">
    <h3 class="salad-name">Main Mein Salad<span class="price">9.95</span></h3>
    <p class="desc">Cold lo mein noodles with chicken breast and vegetables in a spicy peanut dressing.</p>
  </article>
  <article class="salad" style="left:790px;">
    <h3 class="salad-name">Sesame Chicken Salad<span class="price">9.95</span></h3>
    <p class="desc">Shredded lettuce, chicken scallions, breast, red cabbage, carrots, browncrunchies, fresh oranges, scallions, and sesame dressing.</p>
  </article>

  <div class="rule-h"></div>

  <h2 class="section-title" style="top:275px;">CHICKEN</h2>
  <p class="section-note" style="left:110px; width:424px; top:310px;">For white meat chicken, add $1.00. Enjoy a Half Chinese Chicken Salad or Plain Fried Rice with any entrée for $5.50 Can replace Chicken with Tofu for $1.50</p>

  <div class="rule-v"></div>

  <section class="column column--left">
    <article class="item"><div class="item-head"><span>Orange Chicken</span><span>11.95</span></div>
      <p class="desc">Crispy chicken breast with onions and red and green bell peppers in a tangy orange sauce.</p></article>
    <article class="item"><div class="item-head"><span>General Tso's Chicken</span><span>11.75</span></div>
      <p class="desc">Crispy dark meat chicken with chili peppers in a spicy tangerine sauce topped with scallions.</p></article>
    <article class="item"><div class="item-head"><span>Kung Pao Chicken</span><span>11.95</span></div>
      <p class="desc">Dark meat chicken with red bell peppers, peanuts, and water chestnuts in spicy red sauce.</p></article>
    <article class="item"><div class="item-head"><span>Chicken Lettuce Cups</span><span>11.75</span></div>
      <p class="desc">Minced white meat chicken with bell peppers, water chestnuts, black mushrooms, pine nuts, and white crunchies. Served with four lettuce cups.</p></article>
    <article class="item"><div class="item-head"><span>Chicken With Asparagus</span><span>11.95</span></div>
      <p class="desc">Chicken breast with asparagus and carrots in a lemon white wine sauce.</p></article>
    <article class="item"><div class="item-head"><span>Chicken With Snow Peas</span><span>11.75</span></div>
      <p class="desc desc--flush">Chicken breast served with snow peas, fresh mushrooms, carrots, and sliced garlic.</p></article>
  </section>

  <section class="column column--right">
    <article class="item"><div class="item-head"><span>Teriyaki Chicken Bowl</span><span>11.95</span></div>
      <p class="desc">Dark meat chicken glazed in Teriyaki sauce placed over a bed of rice.</p></article>
    <article class="item"><div class="item-head"><span>Tangerine Chicken</span><span>11.75</span></div>
      <p class="desc">Crispy chicken breast topped with scallions in a tangerine sauce.</p></article>
    <article class="item"><div class="item-head"><span>Almond Chicken</span><span>11.95</span></div>
      <p class="desc">Dark meat chicken with bamboo shoots, celery, water chestnuts, and toasted almonds. Prepared regularly or mandarin-Style.</p></article>
    <article class="item"><div class="item-head"><span>Lemon Chicken</span><span>11.75</span></div>
      <p class="desc">Crispy chicken breast marinated in garlic and ginger; served with a tart lemon sauce on the side.</p></article>
    <article class="item"><div class="item-head"><span>Cashew Chicken</span><span>11.95</span></div>
      <p class="desc">Chicken breast, zucchini, onions, garlic, ginger, and cashews tossed in an oyster sauce.</p></article>
    <article class="item"><div class="item-head"><span>Curry Chicken</span><span>11.95</span></div>
      <p class="desc">Chicken breast with potatoes, onions, green peas, and carrots in a curry sauce.</p></article>
    <article class="item"><div class="item-head"><span>Sweet And Sour Chicken</span><span>11.50</span></div>
      <p class="desc">Crispy chicken breast, bell peppers, onions, and pineapple in a sweet and sour sauce.</p></article>
  </section>

  <div class="brand" style="left:18px;"><span class="brand-mark"></span>Lo Mara</div>
  <div class="brand" style="left:1100px;"><span class="brand-mark"></span>Lo Mara</div>
</main>
</body>
</html>
```